Business cards, poster and standing banners for Brindlefest.org needed under 48h!

Hi Genius designers,
I have a seemingly very simple project, I am organizing a open source hardware hackathon (www.brindlefest.org) and need 6 deliverables:
1) a better looking png logo with transparent background (one light grey, one dark grey color. Only the middle Anarchy A have to remain red) (deadline March 18)
2) a better looking square picture (for social media identity) (deadline March 18)
3) business cards (deadline March 18) (name, email, mobile, twitter, www.brindlefest.org)
4) A3 poster (deadline March 18), should include:
- Tagline: Non-profit Open Source Hardware Hardware
- Date: March 28-30
- Venue: Gearloft Bayside Annex, 712 Pelling Rd, San Carlos
- Join the Hardware renaissance!
- www.brindlefest.org
- QR code (attached)
5) standard standing banners (deadline March 20)
I attached existing logo just need it to be better, and a background picture to use for all these marketing materials. Just need someone to make all these very professional.
Attached:
- existing logo
- existing square image for social media identity
- bakcground
- QR code to include in A3 poster
Updates
Please use existing logo, i am not looking for a new logo, just need a professional version of the existing logo (anarchy A in red)
20-35 entrepreneurs, new generation of hardware engineers, makers
Marketing

```html
<!DOCTYPE html>
<html lang="en">
<head>
<meta charset="utf-8">
<title>Brindlefest Business Card</title>
<link rel="stylesheet" href="https://fonts.googleapis.com/css2?family=Fredoka:wght@600&family=Source+Sans+3:wght@400;600&display=swap">
<style>
  :root {
    --backdrop: #e9e6e2;
    --card-white: #ffffff;
    --card-white-edge: #e4e5e7;
    --brand-grey: #4b4b4d;
    --brand-red: #ed1c24;
    --red-tint: #f2493d;
    --ink-light: #ffffff;
    --shadow: rgba(0, 0, 0, 0.18);
  }
  * { margin: 0; padding: 0; box-sizing: border-box; }
  html, body {
    width: 1200px;
    height: 941px;
    overflow: hidden;
    background: var(--backdrop);
  }
  .sheet {
    position: relative;
    width: 1200px;
    height: 941px;
  }
  .card {
    position: absolute;
    left: 250px;
    width: 700px;
    height: 400px;
    border-radius: 30px;
    box-shadow: 0 10px 24px var(--shadow);
    overflow: hidden;
  }
  .card--front {
    top: 50px;
    background: radial-gradient(ellipse at 50% 50%, var(--card-white) 20%, var(--card-white-edge) 100%);
    display: flex;
    align-items: center;
    justify-content: center;
  }
  .wordmark {
    display: flex;
    align-items: center;
    gap: 14px;
  }
  .wordmark__dot {
    width: 26px;
    height: 26px;
    border-radius: 50%;
    background: var(--brand-red);
  }
  .wordmark__name {
    font-family: "Fredoka", "Arial Rounded MT Bold", sans-serif;
    font-weight: 600;
    font-size: 66px;
    letter-spacing: 1px;
    color: var(--brand-grey);
  }
  .card--back {
    top: 490px;
    background: var(--brand-red);
    font-family: "Source Sans 3", "Myriad Pro", sans-serif;
    color: var(--ink-light);
  }
  .holder {
    position: absolute;
    left: 430px;
    top: 52px;
    padding-left: 18px;
  }
  .holder__marker {
    position: absolute;
    left: 0;
    top: 8px;
    width: 9px;
    height: 9px;
    background: var(--ink-light);
  }
  .holder__bracket {
    position: absolute;
    left: 4px;
    top: 16px;
    width: 10px;
    height: 22px;
    border-left: 1.5px solid var(--ink-light);
    border-bottom: 1.5px solid var(--ink-light);
  }
  .holder__name {
    font-size: 22px;
    font-weight: 600;
    line-height: 1.15;
  }
  .holder__role {
    font-size: 19px;
    font-weight: 400;
    line-height: 1.2;
  }
  .contacts {
    position: absolute;
    left: 60px;
    bottom: 52px;
    list-style: none;
  }
  .contacts__item {
    display: flex;
    align-items: center;
    gap: 12px;
    font-size: 17px;
    line-height: 1;
    margin-top: 11px;
  }
  .contacts__icon {
    width: 20px;
    height: 20px;
    flex: none;
  }
  .backdrop-mark {
    position: absolute;
    right: 40px;
    bottom: 40px;
    width: 150px;
    height: 150px;
    border-radius: 50%;
    background: var(--red-tint);
    opacity: 0.8;
  }
</style>
</head>
<body>
<main class="sheet">
  <section class="card card--front" aria-label="Card front">
    <div class="wordmark">
      <span class="wordmark__name">BRINDLEFEST</span>
      <span class="wordmark__dot"></span>
    </div>
  </section>

  <section class="card card--back" aria-label="Card back">
    <div class="holder">
      <span class="holder__marker"></span>
      <span class="holder__bracket"></span>
      <p class="holder__name">Person’s Name</p>
      <p class="holder__role">Designation</p>
    </div>

    <ul class="contacts">
      <li class="contacts__item">
        <svg class="contacts__icon" viewBox="0 0 20 20" aria-hidden="true">
          <rect x="5" y="1.5" width="10" height="17" rx="2" fill="none" stroke="#fff" stroke-width="1.6"/>
          <line x1="5" y1="15" x2="15" y2="15" stroke="#fff" stroke-width="1.2"/>
          <circle cx="10" cy="16.8" r="0.9" fill="#fff"/>
        </svg>
        <span>555.018.2744</span>
      </li>
      <li class="contacts__item">
        <svg class="contacts__icon" viewBox="0 0 20 20" aria-hidden="true">
          <rect x="1.5" y="4.5" width="17" height="11" fill="none" stroke="#fff" stroke-width="1.5"/>
          <polyline points="1.5,4.5 10,11 18.5,4.5" fill="none" stroke="#fff" stroke-width="1.5"/>
        </svg>
        <span>info@brindlefest.org</span>
      </li>
      <li class="contacts__item">
        <svg class="contacts__icon" viewBox="0 0 20 20" aria-hidden="true">
          <circle cx="10" cy="10" r="8.2" fill="none" stroke="#fff" stroke-width="1.5"/>
          <ellipse cx="10" cy="10" rx="3.6" ry="8.2" fill="none" stroke="#fff" stroke-width="1.3"/>
          <line x1="1.8" y1="10" x2="18.2" y2="10" stroke="#fff" stroke-width="1.3"/>
          <line x1="3.2" y1="5.8" x2="16.8" y2="5.8" stroke="#fff" stroke-width="1.1"/>
          <line x1="3.2" y1="14.2" x2="16.8" y2="14.2" stroke="#fff" stroke-width="1.1"/>
        </svg>
        <span>brindlefest.org</span>
      </li>
      <li class="contacts__item">
        <svg class="contacts__icon" viewBox="0 0 20 20" aria-hidden="true">
          <circle cx="10" cy="10" r="7" fill="#fff"/>
        </svg>
        <span>@brindlefest</span>
      </li>
    </ul>

    <div class="backdrop-mark" aria-hidden="true"></div>
  </section>
</main>
</body>
</html>
```